a business advisory consulting website

I need a website 3-5 pages to sell my professional services in IT and Project management Consulting. My company name is Crestline Advisory Consulting. I want it to be device friendly and easy to navigate for the busy executive however intriguing enough.
I have attached some info I drafted on About the company and personal Bio. Also there is a website that I really like that I have attached the initial site pdf and websites that I like are here: https://tollmeradvisors.example, https://quarvelanalytics.example, https://www.dorvikstudylearning.example as examples. Thanks
Updates

Hi Designers, I have uploaded the logo in 3D .png format, to assist in the web design.

Target Market(s)

B2B, governments, IT companies, Project Management companies and Consulting firms, small medium enterprises to large corporate enterprises.

Industry/Entity Type

It Professional

Coding

Coded - Design and coding required

Number of Pages Required

5+ page

Font styles to use
Sans Serif

Requirements
Must have
• Home, About company, the team, what we do and contact us
Nice to have
• Blog
Should not have
• pop ups, flash

```html
<!DOCTYPE html>
<html lang="en">
<head>
<meta charset="utf-8">
<title>Crestline Advisory</title>
<link href="https://fonts.googleapis.com/css2?family=Hind:wght@400;500&family=Montserrat:wght@400;500;600&display=swap" rel="stylesheet">
<style>
:root{
  --red:#e02a2a;
  --red-dark:#b81c1f;
  --navy:#1e2748;
  --navy-deep:#182040;
  --ink:#333844;
  --muted:#4a4f5a;
  --light:#f4f5f7;
  --white:#ffffff;
}
*{margin:0;padding:0;box-sizing:border-box}
html,body{width:1200px;height:3172px;overflow:hidden;background:var(--white)}
body{font-family:"Montserrat",sans-serif;color:var(--ink);position:relative}
.abs{position:absolute}
.heading{font-family:"Hind",sans-serif;font-weight:400;color:var(--navy);letter-spacing:.5px}
.heading .accent{color:var(--red)}
.btn{position:absolute;display:flex;align-items:center;justify-content:center;font-family:"Hind",sans-serif;font-weight:500;font-size:16px;color:var(--white);background:var(--red);border-radius:4px}
.brand{font-family:"Hind",sans-serif;font-weight:500;font-size:34px;line-height:30px;letter-spacing:.5px;display:flex;align-items:center;gap:12px}
.brand .mark{width:26px;height:26px;background:currentColor;flex:none}
.arrow-ico{width:38px;height:38px;flex:none}
.title-row{display:flex;align-items:center;gap:10px}

/* header */
.site-header{top:0;left:0;width:1200px;height:118px;background:var(--white)}
.site-header .brand{left:172px;top:32px;color:var(--navy)}
.contact-strip{right:172px;top:18px;display:flex;gap:14px;align-items:center;font-size:14px;font-weight:500}
.contact-strip .dot{width:36px;height:36px;border-radius:50%;display:flex;align-items:center;justify-content:center}
.contact-strip .red{color:var(--red)}
.main-nav{right:172px;top:78px;display:flex;gap:22px;font-size:13.5px;font-weight:500;color:var(--navy)}
.main-nav .current{color:var(--red)}

/* hero */
.hero{top:118px;left:0;width:1200px;height:526px;background:linear-gradient(90deg,#2c3a45 0%,#4a5a66 35%,#8a98a6 60%,#b7c1c9 100%)}
.hero h1{position:absolute;left:172px;top:140px;font-family:"Hind",sans-serif;font-weight:400;font-size:54px;color:var(--white)}
.hero p{position:absolute;left:172px;top:224px;width:480px;font-size:15.5px;font-weight:600;line-height:25px;color:var(--white)}
.hero .btn{left:172px;top:302px;width:117px;height:54px;background:transparent;border:2px solid var(--white);font-size:18px}

/* about */
.about{top:644px;left:0;width:1200px;height:418px}
.about .title-row{position:absolute;left:172px;top:62px}
.about .heading{font-size:44px}
.body-copy{font-size:12.5px;line-height:24.6px;color:var(--muted)}
.about .body-copy{position:absolute;left:172px;top:120px;width:470px}
.about .body-copy p+p{margin-top:6px}
.about .btn{left:172px;top:316px;width:101px;height:48px}

/* why */
.why{top:1062px;left:0;width:1200px;height:521px;background:linear-gradient(90deg,#e9ecf0 0%,#fafafa 30%,#fafafa 70%,#eceff3 100%);text-align:center}
.why .title-row{position:absolute;left:0;width:1200px;top:108px;justify-content:center}
.why .heading{font-size:44px}
.why .body-copy{position:absolute;left:172px;width:856px;color:var(--ink)}
.why .lead{position:absolute;left:0;width:1200px;top:244px;font-size:16.5px;font-weight:500;color:var(--red)}
.why .btn{left:549px;top:358px;width:101px;height:48px}

/* services */
.services{top:1583px;left:0;width:1200px;height:489px}
.service-title{position:absolute;font-family:"Hind",sans-serif;font-size:37px;line-height:43px;color:var(--white);display:flex;gap:10px}

/* bio */
.bio{top:2072px;left:0;width:1200px;height:552px;background:var(--light)}
.bio .portrait{position:absolute;left:136px;top:66px;width:326px;height:486px;border-radius:150px 150px 0 0;background:linear-gradient(180deg,#c9ccd1 0%,#3b4252 45%,#262c3a 100%)}
.bio .title-row{position:absolute;left:466px;top:128px}
.bio .heading{font-size:44px}
.bio .body-copy{position:absolute;left:515px;top:191px;width:513px}
.bio .body-copy p+p{margin-top:6px}
.bio .btn{left:516px;top:418px;width:100px;height:48px}

/* footer */
.site-footer{top:2624px;left:0;width:1200px;height:548px;background:var(--navy-deep);border-top:3px solid var(--red);color:var(--white)}
.site-footer .brand{left:172px;top:84px;color:var(--white);font-size:38px;line-height:34px}
.socials{right:172px;top:88px;display:flex;gap:28px}
.socials span{width:44px;height:44px;border-radius:50%;background:var(--white)}
.rule{left:172px;width:856px;height:1px;background:#c8cbd4}
.col-title{font-family:"Hind",sans-serif;font-size:22px;top:262px}
.quick{left:172px;top:303px;font-size:13px;line-height:25px}
.footer-about{left:389px;top:303px;width:306px;font-size:12px;line-height:25px;text-align:justify}
.footer-contact{left:796px;top:312px;font-size:14px;font-weight:600}
.footer-contact .row{display:flex;align-items:center;gap:12px;height:36px;margin-bottom:24px}
.footer-contact .ring{width:36px;height:36px;border:1.5px solid var(--white);border-radius:50%;display:flex;align-items:center;justify-content:center}
.copyright{left:0;width:1200px;top:512px;text-align:center;font-size:13px}
</style>
</head>
<body>

<header class="site-header abs">
  <div class="brand abs"><span class="mark"></span><span>CRESTLINE<br>ADVISORY</span></div>
  <div class="contact-strip abs">
    <span class="dot" style="background:var(--navy)"><svg width="18" height="14" viewBox="0 0 18 14"><rect x="1" y="1" width="16" height="12" rx="2" fill="none" stroke="#fff" stroke-width="1.6"/><path d="M1.5 2 9 8l7.5-6" fill="none" stroke="#fff" stroke-width="1.6"/></svg></span>
    <span>MAIL: info@crestline.example</span>
    <span class="dot" style="background:var(--red);margin-left:6px"><svg width="18" height="18" viewBox="0 0 24 24"><path d="M6.6 10.8a15 15 0 0 0 6.6 6.6l2.2-2.2c.3-.3.7-.4 1-.2 1.1.4 2.3.6 3.6.6.6 0 1 .4 1 1V20c0 .6-.4 1-1 1A17 17 0 0 1 3 4c0-.6.4-1 1-1h3.5c.6 0 1 .4 1 1 0 1.2.2 2.4.6 3.6.1.3 0 .7-.2 1z" fill="#fff"/></svg></span>
    <span>CALL: <span class="red">+123 555 0142</span></span>
  </div>
  <nav class="main-nav abs">
    <span class="current">HOME</span><span>ABOUT COMPANY</span><span>THE TEAM</span><span>WHAT WE DO</span><span>CONTACT US</span>
  </nav>
</header>

<section class="hero abs" role="img" aria-label="Photo of two consultants reviewing work on a laptop in a bright office">
  <h1>CRESTLINE ADVISORY</h1>
  <p>We are a specialist operational excellence firm, delivering consulting and advisory services.</p>
  <span class="btn">Read More</span>
</section>

<section class="about abs">
  <div class="title-row">
    <svg class="arrow-ico" viewBox="0 0 38 38"><path d="M4 34 32 6M14 6h18v18" fill="none" stroke="var(--red)" stroke-width="4"/></svg>
    <h2 class="heading">ABOUT <span class="accent">US</span></h2>
  </div>
  <div class="body-copy">
    <p>We are a specialist operational excellence firm, delivering consulting and advisory services in six core capabilities, across all industries and all business lines to improve performance, efficiency, profitability, automation and scalability, for clients across Australia.</p>
    <p>We're known for our pragmatism, in depth analysis, strategic insight and nurturing long-term client self-sufficiency. We approach business consulting differently, with a Genuine Client Partnership model.</p>
  </div>
  <span class="btn">Read More</span>
  <svg class="abs" style="left:0;top:0" width="1200" height="418" role="img" aria-label="Red-toned image of rising bar charts over a laptop">
    <defs><linearGradient id="aboutRed" x1="0" y1="1" x2="1" y2="0"><stop offset="0" stop-color="#c81e22"/><stop offset="1" stop-color="#e8403a"/></linearGradient></defs>
    <polygon points="653,418 1075,0 1200,0 1200,418" fill="url(#aboutRed)"/>
  </svg>
</section>

<section class="why abs" role="img" aria-label="Faint background of financial charts">
  <div class="title-row">
    <svg class="arrow-ico" viewBox="0 0 38 38"><path d="M4 34 32 6M14 6h18v18" fill="none" stroke="var(--red)" stroke-width="4"/></svg>
    <h2 class="heading">WHY WE <span class="accent">EXIST</span></h2>
  </div>
  <p class="body-copy" style="top:183px">Our aim at Tollmer Capital is to be a leading strategy and financial advisory firm across the continent solving complex management problems for small and medium sized enterprises across a wide range of industries.</p>
  <p class="lead">We help you scale your business operations to become highly profitable</p>
  <p class="body-copy" style="top:287px">We offer your organization cutting-edge expertise leveraging on first-class, strategic and financial insights that help you simplify and structure your processes to become a lean efficient enterprise.</p>
  <span class="btn">Read More</span>
</section>

<section class="services abs">
  <svg class="abs" style="left:0;top:0" width="1200" height="489">
    <g role="img" aria-label="Red-toned photo of a government workspace">
      <polygon points="0,0 716,0 296,429 0,429" fill="var(--red)"/>
    </g>
    <g role="img" aria-label="Navy-toned image of technology growth charts">
      <polygon points="740,0 1200,0 1200,489 259,489" fill="var(--navy)"/>
    </g>
    <polygon points="535,0 690,0 480,210" fill="var(--navy)"/>
  </svg>
  <div class="service-title" style="left:172px;top:40px">
    <svg width="38" height="38" viewBox="0 0 38 38" style="margin-top:6px"><path d="M4 34 32 6M14 6h18v18" fill="none" stroke="#fff" stroke-width="4"/></svg>
    <span>PROCESS<br>IMPROVEMENT<br>WITHIN<br>GOVERNMENT</span>
  </div>
  <svg class="abs" style="left:222px;top:246px" width="70" height="66" viewBox="0 0 70 66"><g fill="none" stroke="#fff" stroke-width="2.5"><rect x="14" y="4" width="42" height="46" rx="3"/><rect x="27" y="1" width="16" height="8" rx="2"/><path d="M22 20h26M22 28h26M22 36h18"/><path d="M4 50h62v6a4 4 0 0 1-4 4H8a4 4 0 0 1-4-4z"/></g></svg>
  <svg class="abs" style="left:775px;top:178px" width="68" height="58" viewBox="0 0 68 58"><g fill="none" stroke="#fff" stroke-width="2.2"><rect x="3" y="3" width="62" height="40" rx="3"/><path d="M24 43v8M44 43v8M16 53h36"/><path d="M12 34V26M18 34V20M24 34v-6"/><circle cx="44" cy="20" r="8"/><circle cx="44" cy="20" r="3"/></g></svg>
  <div class="service-title" style="left:728px;top:276px">
    <svg width="38" height="38" viewBox="0 0 38 38" style="margin-top:6px"><path d="M4 34 32 6M14 6h18v18" fill="none" stroke="#fff" stroke-width="4"/></svg>
    <span>TECHNOLOGY<br>ANALYSIS<br>WITHIN<br>HEALTHCARE</span>
  </div>
</section>

<section class="bio abs">
  <div class="portrait" role="img" aria-label="Portrait photo of the founder in a dark suit"></div>
  <div class="title-row">
    <svg class="arrow-ico" viewBox="0 0 38 38"><path d="M4 34 32 6M14 6h18v18" fill="none" stroke="var(--red)" stroke-width="4"/></svg>
    <h2 class="heading">DANIEL ASHWORTH <span class="accent">BIO</span></h2>
  </div>
  <div class="body-copy">
    <p>Daniel Ashworth is an IT professional with more than 20 years of experience turning business initiatives into technology solutions. His expertise has been identifying deficiencies and developing or facilitating the best solutions for an outcome that is satisfactory to all stakeholders involved</p>
    <p>Daniel improves business processes as older organizations restructure or migrate to newer technologies. He bridges the gap between the actual people in these organizations transitioning and the new technologies they seek which is a value add to any organization's success.</p>
  </div>
  <span class="btn">Read More</span>
</section>

<footer class="site-footer abs">
  <div class="brand abs"><span class="mark"></span><span>CRESTLINE<br>ADVISORY</span></div>
  <div class="socials abs"><span></span><span></span><span></span><span></span></div>
  <div class="rule abs" style="top:195px"></div>
  <h3 class="col-title abs" style="left:172px">Quick Links</h3>
  <h3 class="col-title abs" style="left:389px">About Us</h3>
  <h3 class="col-title abs" style="left:796px">Contact Us</h3>
  <ul class="quick abs" style="list-style:none">
    <li>Home</li><li>About company</li><li>The team</li><li>What we do</li><li>Contact us</li>
  </ul>
  <p class="footer-about abs">We are a specialist operational excellence firm, delivering consulting and advisory services in six core capabilities, across all industries and all business lines to improve performance, efficiency, profitability, automation.</p>
  <div class="footer-contact abs">
    <div class="row"><span class="ring"><svg width="16" height="12" viewBox="0 0 18 14"><rect x="1" y="1" width="16" height="12" rx="2" fill="none" stroke="#fff" stroke-width="1.6"/><path d="M1.5 2 9 8l7.5-6" fill="none" stroke="#fff" stroke-width="1.6"/></svg></span><span>MAIL: info@crestline.example</span></div>
    <div class="row"><span class="ring"><svg width="16" height="16" viewBox="0 0 24 24"><path d="M6.6 10.8a15 15 0 0 0 6.6 6.6l2.2-2.2c.3-.3.7-.4 1-.2 1.1.4 2.3.6 3.6.6.6 0 1 .4 1 1V20c0 .6-.4 1-1 1A17 17 0 0 1 3 4c0-.6.4-1 1-1h3.5c.6 0 1 .4 1 1 0 1.2.2 2.4.6 3.6.1.3 0 .7-.2 1z" fill="none" stroke="#fff" stroke-width="1.6"/></svg></span><span>CALL: +123 555 0142</span></div>
  </div>
  <div class="rule abs" style="top:465px"></div>
  <p class="copyright abs">Copyrights @ 2020 Crestline Advisory. All Rights Reserved.</p>
</footer>

</body>
</html>
```